KVM Contracting services . Building and maintenance services, optic fibre installation

Business cards and logo design.I need a logo that I can use on business cards ,workwear and on my vehicles. I would like the KVM to be the main or larger text and contracting services to be the smaller or less important text.I like monograms, modern designs and repeating patterns symbols. I am also a Gemini and my favourite number is 22 so if this can be any inspiration to help with the design. Am thinking of the using German flag colours as a his is my family’s heritage. And the other 2 main colours I wear is black and white.But any ideas are appreciated.I do not need a design that is trade specific but a design that could be used for any business.

Target Market(s)

General public

Contact Information for Business Card

KVM Contracting Services ( front of business card)

(Back of business card)
Darren Holtwick
0451907326
Maintenance services
Optic fibre and data installation

Logo Text

Logo can just be pattern or monogram or incorporate KVM . I like the gemini star sign and the number 22

Colors
ec1f27
000000
fbee3e
ffffff

Requirements
Must have
• Logo and KVM Contracting Services on the front of business card
Nice to have
• Possible use of German flag colours.
• Modern design.
• Design to be able to be used on black or white background as I want to put it on clothing

```html
<!DOCTYPE html>
<html lang="en">
<head>
<meta charset="utf-8">
<title>KVM Contracting Services – Business Cards</title>
<link rel="stylesheet" href="https://fonts.googleapis.com/css2?family=Lato:wght@400;700;900&family=Oswald:wght@500&display=swap">
<style>
  :root {
    --bg: #2b2b2b;
    --card-black: #0a0a0a;
    --card-white: #ffffff;
    --red: #ec1f27;
    --yellow: #fbee3e;
    --ink: #1a1a1a;
    --white: #ffffff;
  }
  * { box-sizing: border-box; margin: 0; padding: 0; }
  html, body { width: 1200px; height: 930px; overflow: hidden; }
  body { background: var(--bg); font-family: "Lato", sans-serif; position: relative; }

  .card {
    position: absolute;
    width: 620px; height: 360px;
    border-radius: 18px;
    box-shadow: 0 18px 40px rgba(0,0,0,.45);
  }

  /* Front */
  .card--front { left: 70px; top: 80px; background: var(--card-black); }
  .brand {
    position: absolute; left: 190px; top: 90px;
    display: flex; align-items: center; gap: 16px;
  }
  .brand__mark { width: 22px; height: 22px; background: var(--red); flex: none; }
  .brand__name { color: var(--white); font-weight: 900; line-height: 1; }
  .brand__kvm { display: block; font-size: 96px; letter-spacing: 2px; }
  .brand__sub { display: block; font-size: 20px; letter-spacing: 1px; margin-top: 6px; text-transform: uppercase; }
  .services { position: absolute; left: 190px; top: 250px; text-transform: uppercase; letter-spacing: 1px; }
  .services__main { color: var(--yellow); font-size: 15px; }
  .services__sub { color: var(--white); font-size: 15px; margin-top: 4px; }

  /* Back */
  .card--back { left: 510px; top: 490px; background: var(--card-white); color: var(--ink); }
  .person { position: absolute; left: 50px; top: 118px; text-align: right; width: 250px; }
  .person__name { font-family: "Oswald", sans-serif; font-weight: 500; color: var(--red); font-size: 36px; line-height: 1; letter-spacing: .5px; text-transform: uppercase; }
  .person__role { font-size: 17px; margin-top: 4px; }
  .divider { position: absolute; left: 320px; top: 110px; width: 1.5px; height: 72px; background: var(--ink); }
  .contacts { position: absolute; left: 340px; top: 110px; list-style: none; font-size: 15px; }
  .contacts li { display: flex; align-items: center; gap: 8px; height: 24px; }
  .contacts svg { width: 12px; height: 12px; flex: none; }
  .address { position: absolute; left: 0; right: 0; bottom: 60px; text-align: center; font-size: 16px; }
</style>
</head>
<body>

  <section class="card card--front" aria-label="Business card front">
    <div class="brand">
      <span class="brand__mark"></span>
      <div class="brand__name">
        <span class="brand__kvm">KVM</span>
        <span class="brand__sub">Contracting Services</span>
      </div>
    </div>
    <div class="services">
      <p class="services__main">Maintenance Services</p>
      <p class="services__sub">Optic Fibre and Data Installation</p>
    </div>
  </section>

  <section class="card card--back" aria-label="Business card back">
    <div class="person">
      <p class="person__name">Darren Holtwick</p>
      <p class="person__role">Director</p>
    </div>
    <span class="divider"></span>
    <ul class="contacts">
      <li>
        <svg viewBox="0 0 12 12"><path d="M2.5 1 L4.5 1 L5 3.5 L3.8 4.3 Q4.8 6.8 7.7 8.2 L8.5 7 L11 7.5 L11 9.5 Q10.5 11 9 11 Q1 10 1 2.5 Q1 1 2.5 1Z" fill="var(--red)"/></svg>
        0451907326
      </li>
      <li>
        <svg viewBox="0 0 12 12"><rect x="1" y="2.5" width="10" height="7" fill="none" stroke="var(--red)" stroke-width="1.2"/><path d="M1 2.5 L6 6.5 L11 2.5" fill="none" stroke="var(--red)" stroke-width="1.2"/></svg>
        KVM@kvmcontracting.example
      </li>
      <li>
        <svg viewBox="0 0 12 12"><circle cx="6" cy="6" r="5" fill="none" stroke="var(--red)" stroke-width="1.2"/><ellipse cx="6" cy="6" rx="2.2" ry="5" fill="none" stroke="var(--red)" stroke-width="1"/><path d="M1 6 H11" stroke="var(--red)" stroke-width="1"/></svg>
        www.kvmcontracting.example
      </li>
    </ul>
    <p class="address">18 Birchwood Lane, Maple Ridge, FL 32099, USA</p>
  </section>

</body>
</html>
```